Pepper & Palm Business Card FUN & EXCITING

Here is the Information for the Card:
Jaswinder Bains (Ravi)
E: RaviBains@postlark.com
C: (480) 555-0147
www.PepperPalmLV.com

We don't want traditional Indian cliche, We a playful bold and fun business card.

Files: https://files.cloudvessel.net/share/folders/7TqRmXpZ2vKa9LwBn4YcHd3JsEf6UoGi?usp=share_link

https://files.cloudvessel.net/share/folders/4MzXaQ8rTw2YbNcVk6PsLe5GhJdR3FoU?usp=share_link

Target Market(s)

Las Vegas Local Restaurant

Industry/Entity Type

Indian Restaurant

Contact Information for Business Card

Name, Email, Cell Phone, Company Logo

```html
<!DOCTYPE html>
<html lang="en">
<head>
<meta charset="utf-8">
<title>Pepper &amp; Palm – Business Card</title>
<link rel="stylesheet" href="https://fonts.googleapis.com/css2?family=Anton&family=Oleo+Script:wght@700&family=Oswald:wght@600&family=Playfair+Display:ital@1&display=swap">
<style>
  :root {
    --backdrop: #2e2e2e;
    --cream: #fdf3cf;
    --saffron: #f6a623;
    --saffron-deep: #e9901f;
    --pink: #dc6a8f;
    --rust: #e87a2a;
    --ink: #111111;
    --brown: #5a3a2a;
    --social-blue: #3b5aa0;
    --social-magenta: #d6246e;
    --social-red: #d32323;
    --globe-green: #2e9a3e;
  }
  * { box-sizing: border-box; margin: 0; padding: 0; }
  html, body { width: 1200px; height: 689px; overflow: hidden; }
  body {
    background: var(--backdrop);
    position: relative;
    font-family: "Oswald", sans-serif;
  }
  .card {
    position: absolute;
    top: 190px;
    width: 540px;
    height: 309px;
    border-radius: 22px;
    overflow: hidden;
  }

  /* ---------- Front: logo side ---------- */
  .card--front { left: 40px; background: var(--saffron); }
  .card--front .panel {
    position: absolute;
    inset: 22px;
    background: var(--cream);
    border-radius: 26px;
  }
  .brand-logo {
    position: absolute;
    right: 28px;
    top: 40px;
    width: 250px;
    font-family: "Anton", sans-serif;
    font-size: 62px;
    line-height: 0.95;
    color: var(--ink);
    text-transform: uppercase;
    text-align: right;
  }
  .brand-city {
    position: absolute;
    right: 30px;
    top: 196px;
    font-family: "Playfair Display", serif;
    font-style: italic;
    font-size: 15px;
    color: var(--ink);
  }
  .front-art {
    position: absolute;
    left: 120px;
    top: 40px;
    width: 140px;
    height: 190px;
    border-radius: 70px;
    background: radial-gradient(circle at 50% 40%, #ffffff 0%, #f2e2bf 55%, #eea15c 100%);
  }
  .tagline {
    position: absolute;
    left: 108px;
    top: 240px;
    width: 170px;
    text-align: center;
    font-family: "Playfair Display", serif;
    font-style: italic;
    font-size: 13px;
    color: var(--ink);
  }
  .socials {
    position: absolute;
    left: 44px;
    top: 56px;
    list-style: none;
    display: flex;
    flex-direction: column;
    gap: 10px;
  }
  .socials li {
    display: flex;
    align-items: center;
    gap: 6px;
    font-size: 11px;
    color: var(--ink);
  }
  .socials .dot { width: 30px; height: 30px; border-radius: 50%; }
  .dot--chatterly { background: var(--social-blue); }
  .dot--snapgram { background: var(--social-magenta); }
  .dot--tastebud { background: var(--social-red); }

  /* ---------- Back: contact side ---------- */
  .card--back { left: 620px; background: var(--saffron-deep); }
  .card--back .bands { position: absolute; inset: 0; }
  .holder-name {
    position: absolute;
    left: 24px;
    top: 52px;
    font-family: "Oleo Script", cursive;
    font-weight: 700;
    font-size: 42px;
    color: var(--ink);
    white-space: nowrap;
  }
  .back-art {
    position: absolute;
    right: 26px;
    top: 120px;
    width: 200px;
    height: 150px;
    border-radius: 75px;
    background: radial-gradient(circle at 50% 45%, #ffffff 0%, #f3e6c6 50%, #ef8a3a 100%);
  }
  .contacts {
    position: absolute;
    left: 26px;
    bottom: 22px;
    list-style: none;
    display: flex;
    flex-direction: column;
    gap: 6px;
  }
  .contacts li {
    display: flex;
    align-items: center;
    gap: 10px;
    font-size: 16px;
    letter-spacing: 0.3px;
    color: var(--ink);
  }
  .contacts .icon {
    width: 24px; height: 24px;
    border-radius: 50%;
    border: 2px solid #fff;
    display: flex; align-items: center; justify-content: center;
  }
  .icon--phone { background: var(--rust); }
  .icon--mail { background: var(--pink); }
  .icon--web { background: var(--globe-green); }
  .icon--pin { background: var(--brown); }
  .contacts svg { width: 12px; height: 12px; }
</style>
</head>
<body>

<section class="card card--front" aria-label="Business card front">
  <div class="panel">
    <ul class="socials">
      <li><span class="dot dot--chatterly"></span>Chatterly</li>
      <li><span class="dot dot--snapgram"></span>Snapgram</li>
      <li><span class="dot dot--tastebud"></span>Tastebud</li>
    </ul>
    <div class="front-art" role="img" aria-label="Cartoon bread and curry bowl mascots walking together with hearts"></div>
    <p class="tagline">“A match made in heaven”</p>
    <h1 class="brand-logo">Pepper &amp; Palm</h1>
    <p class="brand-city">Las Vegas, NV</p>
  </div>
</section>

<section class="card card--back" aria-label="Business card back">
  <svg class="bands" viewBox="0 0 540 309" preserveAspectRatio="none" aria-hidden="true">
    <path d="M0 0 H540 V40 Q420 120 250 170 Q120 205 0 190 Z" fill="var(--pink)"/>
    <path d="M0 190 Q120 205 250 170 Q420 120 540 40 V52 Q420 132 250 182 Q120 218 0 204 Z" fill="var(--rust)"/>
  </svg>
  <h2 class="holder-name">Jaswinder Bains (Ravi)</h2>
  <div class="back-art" role="img" aria-label="Cartoon curry bowl and bread mascots strolling arm in arm"></div>
  <ul class="contacts">
    <li><span class="icon icon--phone"><svg viewBox="0 0 12 12"><rect x="3" y="0.5" width="6" height="11" rx="1.2" fill="none" stroke="#fff" stroke-width="1.2"/><circle cx="6" cy="9.5" r="0.7" fill="#fff"/></svg></span>(480) 555-0147</li>
    <li><span class="icon icon--mail"><svg viewBox="0 0 12 12"><rect x="0.8" y="2.5" width="10.4" height="7" fill="none" stroke="#fff" stroke-width="1.2"/><path d="M1 3 L6 7 L11 3" fill="none" stroke="#fff" stroke-width="1.2"/></svg></span>RaviBains@postlark.com</li>
    <li><span class="icon icon--web"><svg viewBox="0 0 12 12"><circle cx="6" cy="6" r="5" fill="none" stroke="#fff" stroke-width="1.2"/><ellipse cx="6" cy="6" rx="2.2" ry="5" fill="none" stroke="#fff" stroke-width="1"/><line x1="1" y1="6" x2="11" y2="6" stroke="#fff" stroke-width="1"/></svg></span>www.PepperPalmLV.com</li>
    <li><span class="icon icon--pin"><svg viewBox="0 0 12 12"><path d="M6 11.5 C3 8 2 6 2 4.5 A4 4 0 0 1 10 4.5 C10 6 9 8 6 11.5 Z" fill="#fff"/><circle cx="6" cy="4.6" r="1.5" fill="var(--brown)"/></svg></span>Las Vegas, NV</li>
  </ul>
</section>

</body>
</html>
```